Street Sign Project - Attract Customers

We need a street sign designed to display out the front of the building. It design will need to be 1800mm wide x 900mm high. We need to show potential customers where we are inviting. Some of the attachments are for inspiration. The sign will be printed on a sheet of aluminum. if you have a good look at our web site which is www.tv-r.com.au you should get a good feeling about the company and what we do.

Target Market(s)

Construction companies, landscaping and civil earth moving companies who may drive past our business

Industry/Entity Type

Building

Font styles to use
Sans Serif

Colors
ffffff
3277b5
000000

Requirements
Must have
• Company logo must be the main focus point
• The number "38" on the sign to show street number (300mm high)
• phone number - (02) 9413 5860
• web address - www.tv-r.com.au
• I have loaded pictures i would like to see used in the sign
Nice to have
• Banner picture as attached
Should not have
• Bright colours. Please use our blue colour where possible

```html
<!DOCTYPE html>
<html lang="en">
<head>
<meta charset="utf-8">
<title>Street Sign – Lifting &amp; Moving Systems</title>
<link rel="stylesheet" href="https://fonts.googleapis.com/css2?family=Archivo+Black&family=Oswald:wght@500&family=Poppins:wght@700&display=swap">
<style>
  :root {
    --brand-blue: #1a4f9c;
    --white: #ffffff;
    --photo-earth: #8a7f6e;
    --photo-steel: #b9bcbf;
    --photo-timber: #a88a5c;
    --photo-green: #7f9a72;
    --photo-red: #b5584a;
  }
  * { margin: 0; padding: 0; box-sizing: border-box; }
  html, body { width: 1200px; height: 600px; overflow: hidden; background: var(--white); }
  .sign { position: relative; width: 1200px; height: 600px; background: var(--white); }

  .street-panel { position: absolute; left: 0; top: 0; width: 314px; height: 600px; background: var(--brand-blue); }
  .street-panel svg { display: block; }

  .photo-strip { position: absolute; left: 377px; top: 36px; display: flex; gap: 2px; }
  .photo { width: 70px; height: 89px; }
  .photo--earth { background: linear-gradient(160deg, #6f7a63, var(--photo-earth)); }
  .photo--steel { background: linear-gradient(180deg, #e6e7e8, var(--photo-steel)); }
  .photo--timber { background: linear-gradient(90deg, #8fb2c4, var(--photo-timber)); }
  .photo--green { background: linear-gradient(180deg, #c9d6c4, var(--photo-green)); }
  .photo--red { background: linear-gradient(120deg, var(--photo-red), #d9c9b8); }

  .contact { position: absolute; left: 798px; top: 40px; color: var(--brand-blue); font-family: "Poppins", "Century Gothic", sans-serif; font-weight: 700; }
  .contact__phone { font-size: 43px; line-height: 48px; letter-spacing: 1px; }
  .contact__web { font-size: 30px; line-height: 34px; letter-spacing: 0.3px; }

  .company-name { position: absolute; left: 350px; top: 190px; width: 820px; text-align: center; color: var(--brand-blue); font-family: "Archivo Black", "Arial Black", sans-serif; font-weight: 400; }
  .company-name__line { display: block; font-size: 100px; line-height: 118px; letter-spacing: 2px; }
  .company-name__suffix { display: block; font-size: 22px; line-height: 26px; text-align: right; padding-right: 60px; letter-spacing: 1px; }
</style>
</head>
<body>
<main class="sign">
  <section class="street-panel" aria-label="Street number 38">
    <svg width="314" height="600" viewBox="0 0 314 600">
      <text x="162" y="136" text-anchor="middle" fill="#ffffff" font-family="Archivo Black, Arial Black, sans-serif" font-size="50" letter-spacing="3">STREET</text>
      <text x="40" y="532" fill="#ffffff" font-family="Oswald, Arial Narrow, sans-serif" font-weight="500" font-size="450" textLength="238" lengthAdjust="spacingAndGlyphs">38</text>
    </svg>
  </section>

  <div class="photo-strip">
    <div class="photo photo--earth" role="img" aria-label="Photo: worker beside a conveyor on an earthworks site"></div>
    <div class="photo photo--steel" role="img" aria-label="Photo: materials hoist with platform"></div>
    <div class="photo photo--timber" role="img" aria-label="Photo: debris chute on a scaffold"></div>
    <div class="photo photo--green" role="img" aria-label="Photo: hopper lifted by a small crane"></div>
    <div class="photo photo--red" role="img" aria-label="Photo: worker loading rolls onto an inclined lift"></div>
  </div>

  <div class="contact">
    <p class="contact__phone">(02) 9413 5860</p>
    <p class="contact__web">www.tv-r.com.au</p>
  </div>

  <h1 class="company-name">
    <span class="company-name__line">LIFTING</span>
    <span class="company-name__line">&amp; MOVING</span>
    <span class="company-name__line">SYSTEMS</span>
    <span class="company-name__suffix">PTY LTD.</span>
  </h1>
</main>
</body>
</html>
```